Bright Towns Forum PowerPoint Design Template and Sample Deck

The Bright Towns Forum is an international organization that seeks to improve the livability, workability and sustainability of the world’s cities.
We seek a versatile PowerPoint design template with 10 slide types plus a “self-documenting” sample deck. Your design will be used in keynote speeches and workshops around the world.
After the contest is completed, we will ask the winning designer to add 10-20 additional slide types for $75 per slide. We also seek a long-term relationship whereby we can request “custom” slides and/or ask the designer to touch up the slides we build to make them better.
FILES. We have uploaded several files:
2. PALETTE. Shows our official colors.
3 LOGOS. Several individual files with different variations of our logo. Some with our motto, some without.
2. SAMPLE SLIDES. Because we were unable to successfully upload our sample deck, we are making it available via this FileNook link:
https://www.filenook-example.com/s/k7qrtmzp2wd9hxa/The%20Bright%20Towns%20Forum%20Design%20Contest%20Notes.docx?dl=0
Target Market(s)
Mayors, department heads, CIOs, senior executives from technology companies
Industry/Entity Type
Information Technology
Colors
Designer to choose colors to be used in the design.
Requirements
Must have
- Please see uploaded Word document for requirements, nice to haves and should not haves and uploaded palette for color preferences.
Nice to have
- see above
Should not have
- see above

```html
<!DOCTYPE html>
<html lang="en">
<head>
<meta charset="utf-8">
<title>Individual Slides 01d – Bright Towns Forum</title>
<link rel="stylesheet" href="https://fonts.googleapis.com/css2?family=Roboto+Condensed:wght@300;700&family=Open+Sans:ital,wght@0,400;0,600;0,700;1,400&display=swap">
<style>
  :root{
    --heading-pink:#e2b9bc;
    --stage:#a8916a;
    --navy:#13305f;
    --blue:#2d5bb9;
    --blue-soft:#6f8fd8;
    --grey-band:#9a9a9a;
    --section-grey:#6e6e70;
    --section-grey-2:#858589;
    --orange:#f37021;
    --red:#e8432b;
    --amber:#f6a21a;
    --green:#6b9b2e;
    --dark-panel:#232c3d;
    --ink:#777;
    --photo-a:#8a8a8a;
    --photo-b:#6d6a5c;
    --white:#ffffff;
  }
  *{box-sizing:border-box;margin:0;padding:0}
  html,body{width:1200px;height:1200px;overflow:hidden;background:var(--white)}
  .sheet{position:relative;width:1200px;height:1200px}
  .sheet-header{height:262px;text-align:center;font-family:"Roboto Condensed",sans-serif}
  .sheet-title{padding-top:56px;font-size:72px;font-weight:700;color:var(--heading-pink);letter-spacing:1px;line-height:1}
  .sheet-subtitle{margin-top:18px;font-size:30px;font-weight:300;color:var(--heading-pink)}
  .stage{position:absolute;left:0;top:262px;width:1200px;height:938px;background:var(--stage)}
  .slide{position:absolute;width:320px;height:180px;box-shadow:2px 3px 6px rgba(0,0,0,.35);background:var(--white);font-family:"Open Sans",sans-serif}
  .slide svg{display:block;width:320px;height:180px}
  .col-1{left:71px}.col-2{left:445px}.col-3{left:819px}
  .row-1{top:33px}.row-2{top:239px}.row-3{top:460px}.row-4{top:666px}
</style>
</head>
<body>
<div class="sheet">
  <header class="sheet-header">
    <h1 class="sheet-title">INDIVIDUAL SLIDES - 01d</h1>
    <p class="sheet-subtitle">(Bigger size for more details)</p>
  </header>

  <main class="stage">

    <!-- Section divider: pictures -->
    <section class="slide section-divider col-1 row-1">
      <svg viewBox="0 0 320 180">
        <rect width="320" height="180" fill="var(--section-grey)"/>
        <path d="M40 0L140 0L90 90L200 180L110 180L20 90Z" fill="#fff" opacity=".05"/>
        <path d="M150 40L230 110L170 180L110 130Z" fill="#fff" opacity=".04"/>
        <text x="268" y="113" text-anchor="end" font-size="9" font-weight="600" fill="#fff">8  2 Pictures</text>
        <text x="268" y="122" text-anchor="end" font-size="5.5" font-style="italic" fill="#ddd">Slide Ideas...</text>
        <circle cx="292" cy="110" r="5" fill="none" stroke="#ddd" stroke-width=".8"/>
        <path d="M290.5 107.5L294.5 110L290.5 112.5Z" fill="#ddd"/>
      </svg>
    </section>

    <!-- Two pictures slide -->
    <section class="slide two-pictures col-2 row-1">
      <svg viewBox="0 0 320 180">
        <text x="160" y="18" text-anchor="middle" font-size="11.5" font-weight="700" fill="var(--blue)">Two Pictures Slide</text>
        <text x="160" y="27" text-anchor="middle" font-size="6" font-weight="700" fill="var(--blue)" letter-spacing="-.5">•••••</text>
        <text x="24" y="46" font-size="3.2" font-style="italic" fill="var(--ink)">Sample text for the slide introduction goes here. Keep it short, clear and useful for the audience today, please.</text>
        <text x="24" y="53" font-size="3.2" font-style="italic" fill="var(--ink)">Add a second line of supporting detail to frame both pictures below.</text>
        <g role="img" aria-label="Photo: workshop attendees with laptops"><rect x="28" y="60" width="130" height="98" fill="var(--photo-a)"/></g>
        <rect x="28" y="145" width="130" height="13" fill="var(--blue)" opacity=".85"/>
        <text x="93" y="153.5" text-anchor="middle" font-size="4" fill="#fff">Your Title Here</text>
        <g role="img" aria-label="Photo: audience watching a keynote on a projector screen"><rect x="171" y="60" width="131" height="98" fill="var(--photo-b)"/></g>
        <rect x="171" y="145" width="131" height="13" fill="var(--grey-band)" opacity=".85"/>
        <text x="236" y="153.5" text-anchor="middle" font-size="4" fill="#fff">Your Title Here</text>
        <rect y="162" width="320" height="18" fill="var(--navy)"/>
        <text x="11" y="174" font-size="8" fill="#fff">BrightTownsForum</text>
        <text x="294" y="173" text-anchor="end" font-size="3" fill="#fff">BrightTownsForum  |  Copyright 2017</text>
        <circle cx="302" cy="171.5" r="3.5" fill="var(--blue)"/><text x="302" y="172.7" text-anchor="middle" font-size="3" fill="#fff">42</text>
      </svg>
    </section>

    <!-- Two pictures with callout banner -->
    <section class="slide two-pictures-banner col-3 row-1">
      <svg viewBox="0 0 320 180">
        <g role="img" aria-label="Photo: workshop attendees with laptops"><rect x="10" y="18" width="148" height="142" fill="var(--photo-a)"/></g>
        <g role="img" aria-label="Photo: audience watching a keynote on a projector screen"><rect x="160" y="18" width="147" height="142" fill="var(--photo-b)"/></g>
        <rect x="10" y="18" width="148" height="16" fill="var(--blue-soft)"/>
        <rect x="160" y="18" width="147" height="16" fill="var(--grey-band)"/>
        <text x="84" y="29" text-anchor="middle" font-size="7.5" font-weight="600" fill="#fff">Your Title Here</text>
        <text x="234" y="29" text-anchor="middle" font-size="7.5" font-weight="600" fill="#fff">Your Title Here</text>
        <rect x="10" y="160" width="297" height="17" fill="var(--blue-soft)"/>
        <text x="158" y="171" text-anchor="middle" font-size="7.5" font-weight="600" fill="#fff">Enter Your Callout Banner Text Here</text>
      </svg>
    </section>

    <!-- Full-bleed two pictures with footer -->
    <section class="slide two-pictures-full col-1 row-2">
      <svg viewBox="0 0 320 180">
        <g role="img" aria-label="Photo: workshop attendees with laptops"><rect x="0" y="0" width="158" height="137" fill="var(--photo-a)"/></g>
        <g role="img" aria-label="Photo: audience watching a keynote on a projector screen"><rect x="160" y="0" width="160" height="137" fill="var(--photo-b)"/></g>
        <rect x="0" y="0" width="158" height="17" fill="var(--blue-soft)"/>
        <rect x="160" y="0" width="160" height="17" fill="var(--grey-band)"/>
        <text x="75" y="11" text-anchor="middle" font-size="7.5" font-weight="600" fill="#fff">Your Title Here</text>
        <text x="243" y="12" text-anchor="middle" font-size="7.5" font-weight="600" fill="#fff">Your Title Here</text>
        <rect x="0" y="137" width="320" height="19" fill="var(--blue)"/>
        <text x="150" y="149" text-anchor="middle" font-size="7.5" font-weight="600" fill="#fff">Enter Your Callout Banner Text Here</text>
        <rect y="161" width="320" height="19" fill="var(--navy)"/>
        <text x="11" y="173.5" font-size="8" fill="#fff">BrightTownsForum</text>
        <text x="294" y="173" text-anchor="end" font-size="3" fill="#fff">BrightTownsForum  |  Copyright 2017</text>
        <circle cx="302" cy="171.5" r="3.5" fill="var(--blue)"/><text x="302" y="172.7" text-anchor="middle" font-size="3" fill="#fff">42</text>
      </svg>
    </section>

    <!-- Section divider: timeline -->
    <section class="slide section-divider col-1 row-3">
      <svg viewBox="0 0 320 180">
        <rect width="320" height="180" fill="var(--section-grey-2)"/>
        <path d="M40 0L140 0L90 90L200 180L110 180L20 90Z" fill="#fff" opacity=".05"/>
        <path d="M150 40L230 110L170 180L110 130Z" fill="#fff" opacity=".04"/>
        <text x="278" y="113" text-anchor="end" font-size="9" font-weight="600" fill="#fff">9 Timeline</text>
        <text x="278" y="122" text-anchor="end" font-size="5.5" font-style="italic" fill="#ddd">Slide Ideas...</text>
        <circle cx="292" cy="110" r="5" fill="none" stroke="#ddd" stroke-width=".8"/>
        <path d="M290.5 107.5L294.5 110L290.5 112.5Z" fill="#ddd"/>
      </svg>
    </section>

    <!-- Six months timeline -->
    <section class="slide six-months col-2 row-3">
      <svg viewBox="0 0 320 180" font-family="Open Sans, sans-serif">
        <text x="160" y="18" text-anchor="middle" font-size="11.5" font-weight="700" fill="var(--blue)">Six Months Timeline</text>
        <text x="160" y="27" text-anchor="middle" font-size="6" font-weight="700" fill="var(--blue)" letter-spacing="-.5">•••••</text>
        <line x1="0" y1="142" x2="320" y2="142" stroke="#8a7fb0" stroke-width=".7"/>
        <g stroke="#bbb" stroke-width=".4">
          <line x1="57" y1="95" x2="57" y2="142"/><line x1="98" y1="60" x2="98" y2="142"/>
          <line x1="140" y1="95" x2="140" y2="142"/><line x1="181" y1="67" x2="181" y2="142"/>
          <line x1="222" y1="94" x2="222" y2="142"/><line x1="263" y1="61" x2="263" y2="142"/>
        </g>
        <g font-size="3" fill="var(--ink)" text-anchor="middle">
          <text x="57" y="149">JAN</text><text x="98" y="149">FEB</text><text x="140" y="149">MAR</text>
          <text x="181" y="149">APR</text><text x="222" y="149">MAY</text><text x="263" y="149">JUN</text>
        </g>
        <circle cx="57" cy="142" r="1.2" fill="#5b3f98"/><circle cx="98" cy="142" r="1.2" fill="var(--orange)"/>
        <circle cx="140" cy="142" r="1.2" fill="#555"/><circle cx="181" cy="142" r="1.2" fill="var(--amber)"/>
        <circle cx="222" cy="142" r="1.2" fill="#4a7bd0"/><circle cx="263" cy="142" r="1.2" fill="var(--navy)"/>
        <circle cx="57" cy="89" r="6" fill="#7a4aa8"/><path d="M54 90L60 87L57 92Z" fill="#fff"/>
        <circle cx="98" cy="54" r="6" fill="var(--orange)"/><rect x="95.5" y="51" width="5" height="6" rx=".6" fill="none" stroke="#fff" stroke-width=".8"/>
        <circle cx="140" cy="89" r="6" fill="#555"/><path d="M140 85.5L141 88.2L143.8 88.3L141.6 90L142.4 92.7L140 91.1L137.6 92.7L138.4 90L136.2 88.3L139 88.2Z" fill="#fff"/>
        <circle cx="181" cy="61" r="6" fill="var(--amber)"/><circle cx="181" cy="59.5" r="1.6" fill="#fff"/><path d="M177.8 64.5a3.2 2.6 0 0 1 6.4 0Z" fill="#fff"/>
        <circle cx="222" cy="88" r="6" fill="#4a7bd0"/><rect x="219" y="86" width="6" height="4.5" rx=".5" fill="none" stroke="#fff" stroke-width=".8"/>
        <circle cx="263" cy="55" r="6" fill="var(--navy)"/><circle cx="263" cy="55" r="3" fill="none" stroke="#fff" stroke-width=".7"/><line x1="260" y1="55" x2="266" y2="55" stroke="#fff" stroke-width=".5"/>
        <g font-size="3.2" fill="#555" text-anchor="middle">
          <text x="57" y="105">Your Title Here</text><text x="98" y="70">Your Title Here</text>
          <text x="140" y="105">Your Title Here</text><text x="181" y="75">Your Title Here</text>
          <text x="222" y="105">Your Title Here</text><text x="263" y="70">Your Title Here</text>
        </g>
        <g font-size="2.3" font-style="italic" fill="#999" text-anchor="middle">
          <text x="57" y="110">Short note for this month,</text><text x="57" y="113">one more line here.</text>
          <text x="98" y="75">Short note for this month,</text><text x="98" y="78">one more line here.</text>
          <text x="140" y="110">Short note for this month,</text><text x="140" y="113">one more line here.</text>
          <text x="181" y="80">Short note for this month,</text><text x="181" y="83">one more line here.</text>
          <text x="222" y="110">Short note for this month,</text><text x="222" y="113">one more line here.</text>
          <text x="263" y="75">Short note for this month,</text><text x="263" y="78">one more line here.</text>
        </g>
        <rect y="162" width="320" height="18" fill="var(--navy)"/>
        <text x="11" y="174" font-size="8" fill="#fff">BrightTownsForum</text>
        <text x="294" y="173" text-anchor="end" font-size="3" fill="#fff">BrightTownsForum  |  Copyright 2017</text>
        <circle cx="302" cy="171.5" r="3.5" fill="var(--blue)"/><text x="302" y="172.7" text-anchor="middle" font-size="3" fill="#fff">44</text>
      </svg>
    </section>

    <!-- One year timeline -->
    <section class="slide one-year col-3 row-3">
      <svg viewBox="0 0 320 180">
        <text x="160" y="18" text-anchor="middle" font-size="11.5" font-weight="700" fill="var(--blue)">One Year Timeline</text>
        <text x="160" y="27" text-anchor="middle" font-size="6" font-weight="700" fill="var(--blue)" letter-spacing="-.5">•••••</text>
        <g stroke="#e6e6e6" stroke-width=".4">
          <line x1="35" y1="50" x2="290" y2="50"/><line x1="35" y1="60" x2="290" y2="60"/>
          <line x1="35" y1="70" x2="290" y2="70"/><line x1="35" y1="80" x2="290" y2="80"/>
        </g>
        <line x1="30" y1="91" x2="290" y2="91" stroke="#bbb" stroke-width=".8"/>
        <g fill="#fff" stroke="#aaa" stroke-width=".6">
          <circle cx="30" cy="91" r="1.8"/><circle cx="51.6" cy="91" r="1.8"/><circle cx="73.2" cy="91" r="1.8"/><circle cx="94.8" cy="91" r="1.8"/>
          <circle cx="116.4" cy="91" r="1.8"/><circle cx="138" cy="91" r="1.8"/><circle cx="159.6" cy="91" r="1.8"/><circle cx="181.2" cy="91" r="1.8"/>
          <circle cx="202.8" cy="91" r="1.8"/><circle cx="224.4" cy="91" r="1.8"/><circle cx="246" cy="91" r="1.8"/><circle cx="267.6" cy="91" r="1.8"/>
          <circle cx="289" cy="91" r="1.8"/>
        </g>
        <g font-size="2.8" fill="#999" text-anchor="middle">
          <text x="41" y="97">JAN</text><text x="62.5" y="97">FEB</text><text x="84" y="97">MAR</text><text x="105.6" y="97">APR</text>
          <text x="127" y="97">MAY</text><text x="148.8" y="97">JUN</text><text x="170.4" y="97">JUL</text><text x="192" y="97">AUG</text>
          <text x="213.6" y="97">SEP</text><text x="235.2" y="97">OCT</text><text x="256.8" y="97">NOV</text><text x="278.4" y="97">DEC</text>
        </g>
        <rect x="40" y="65" width="3.5" height="25" fill="var(--navy)"/>
        <rect x="63" y="78" width="3.5" height="12" fill="var(--blue)"/>
        <rect x="105" y="63" width="3.5" height="27" fill="#6f9be0"/>
        <rect x="148" y="68" width="3.5" height="22" fill="var(--red)"/>
        <rect x="191" y="70" width="3.5" height="20" fill="var(--amber)"/>
        <rect x="234" y="80" width="3.5" height="10" fill="#666"/>
        <rect x="277" y="62" width="3.5" height="28" fill="#999"/>
        <g font-size="2.6" fill="#888" text-anchor="middle">
          <text x="41.5" y="58">Your Title</text><text x="64.5" y="69">Your Title</text><text x="106.5" y="55">Your Title</text>
          <text x="149.5" y="62">Your Title</text><text x="192.5" y="59">Your Title</text><text x="235.5" y="68">Your Title</text><text x="278.5" y="58">Your Title</text>
        </g>
        <g font-size="3" font-style="italic" fill="var(--ink)">
          <text x="24" y="124">Sample text for the yearly overview goes here. Summarise the key points that matter most to each city team.</text>
          <text x="24" y="131">Use this second line to add context about milestones and goals across the full twelve month plan ahead.</text>
          <text x="24" y="138">Close with a brief note.</text>
        </g>
        <rect y="162" width="320" height="18" fill="var(--navy)"/>
        <text x="11" y="174" font-size="8" fill="#fff">BrightTownsForum</text>
        <text x="294" y="173" text-anchor="end" font-size="3" fill="#fff">BrightTownsForum  |  Copyright 2017</text>
        <circle cx="302" cy="171.5" r="3.5" fill="var(--blue)"/><text x="302" y="172.7" text-anchor="middle" font-size="3" fill="#fff">45</text>
      </svg>
    </section>

    <!-- Key events timeline, dark -->
    <section class="slide key-events-dark col-1 row-4">
      <svg viewBox="0 0 320 180">
        <rect width="320" height="123" fill="var(--dark-panel)"/>
        <text x="160" y="18" text-anchor="middle" font-size="11.5" font-weight="700" fill="#fff">Key Events Timeline</text>
        <text x="160" y="27" text-anchor="middle" font-size="6" font-weight="700" fill="#fff" letter-spacing="-.5">•••••</text>
        <g font-size="3" font-weight="700" fill="#fff" text-anchor="middle">
          <text x="34" y="64">JAN</text><text x="57" y="64">FEB</text><text x="80" y="64">MAR</text><text x="103" y="64">APR</text>
          <text x="126" y="64">MAY</text><text x="149" y="64">JUN</text><text x="172" y="64">JUL</text><text x="195" y="64">AUG</text>
          <text x="218" y="64">SEP</text><text x="241" y="64">OCT</text><text x="264" y="64">NOV</text><text x="287" y="64">DEC</text>
        </g>
        <g stroke="#3d475a" stroke-width=".4">
          <line x1="23" y1="67" x2="298" y2="67"/><line x1="23" y1="74" x2="298" y2="74"/><line x1="23" y1="81" x2="298" y2="81"/>
          <line x1="23" y1="88" x2="298" y2="88"/><line x1="23" y1="95" x2="298" y2="95"/><line x1="23" y1="102" x2="298" y2="102"/><line x1="23" y1="109" x2="298" y2="109"/>
          <line x1="45.5" y1="67" x2="45.5" y2="109"/><line x1="68.5" y1="67" x2="68.5" y2="109"/><line x1="91.5" y1="67" x2="91.5" y2="109"/>
          <line x1="114.5" y1="67" x2="114.5" y2="109"/><line x1="137.5" y1="67" x2="137.5" y2="109"/><line x1="160.5" y1="67" x2="160.5" y2="109"/>
          <line x1="183.5" y1="67" x2="183.5" y2="109"/><line x1="206.5" y1="67" x2="206.5" y2="109"/><line x1="229.5" y1="67" x2="229.5" y2="109"/>
          <line x1="252.5" y1="67" x2="252.5" y2="109"/><line x1="275.5" y1="67" x2="275.5" y2="109"/>
        </g>
        <rect x="24" y="69" width="70" height="3" fill="#3f6fd0"/>
        <rect x="69" y="76" width="66" height="3" fill="var(--orange)"/>
        <rect x="96" y="83" width="65" height="3" fill="#999"/>
        <rect x="146" y="90" width="82" height="3" fill="var(--amber)"/>
        <rect x="114" y="97" width="167" height="3" fill="#4a8fe0"/>
        <rect x="222" y="104" width="74" height="3" fill="#6bbf3a"/>
        <g font-size="3" fill="#888" text-anchor="end">
          <text x="72" y="138">Plan and Conception</text><text x="72" y="149">Analysis</text><text x="72" y="160">Product Design</text>
          <text x="142" y="138">Reviewing</text><text x="142" y="149">Product Development</text><text x="142" y="160">Release</text>
        </g>
        <rect x="75" y="135.5" width="4" height="4" fill="#3f6fd0"/><rect x="75" y="146.5" width="4" height="4" fill="var(--orange)"/>
        <rect x="75" y="157.5" width="4" height="4" fill="#999"/><rect x="145" y="135.5" width="4" height="4" fill="var(--amber)"/>
        <rect x="145" y="146.5" width="4" height="4" fill="#4a8fe0"/><rect x="145" y="157.5" width="4" height="4" fill="#6bbf3a"/>
        <line x1="170" y1="131" x2="170" y2="160" stroke="#ddd" stroke-width=".4"/>
        <text x="173" y="138" font-size="4.5" fill="#999">Final Result</text>
        <g font-size="2.6" fill="#999">
          <text x="173" y="146">Sample body text for the final result goes here with a brief</text>
          <text x="173" y="151">summary of outcomes, lessons learned and the next steps</text>
          <text x="173" y="156">for the team.</text>
        </g>
        <rect y="162" width="320" height="18" fill="var(--navy)"/>
        <text x="11" y="174" font-size="8" fill="#fff">BrightTownsForum</text>
        <text x="294" y="173" text-anchor="end" font-size="3" fill="#fff">BrightTownsForum  |  Copyright 2017</text>
        <circle cx="302" cy="171.5" r="3.5" fill="var(--blue)"/><text x="302" y="172.7" text-anchor="middle" font-size="3" fill="#fff">46</text>
      </svg>
    </section>

    <!-- Key events timeline, light -->
    <section class="slide key-events-light col-2 row-4">
      <svg viewBox="0 0 320 180">
        <text x="160" y="18" text-anchor="middle" font-size="11.5" font-weight="700" fill="var(--blue)">Key Events Timeline</text>
        <text x="160" y="27" text-anchor="middle" font-size="6" font-weight="700" fill="var(--blue)" letter-spacing="-.5">•••••</text>
        <g font-size="3" font-style="italic" fill="var(--ink)">
          <text x="24" y="46">Sample text for the key events overview goes here. Describe the main phases and why each one matters.</text>
          <text x="24" y="53">Add supporting detail on owners, timing and dependencies so every reader can follow the full plan clearly.</text>
          <text x="24" y="60">Finish with a short closing note.</text>
        </g>
        <g font-size="3" fill="#aaa" text-anchor="middle">
          <text x="35" y="82">JAN</text><text x="57.5" y="82">FEB</text><text x="80" y="82">MAR</text><text x="102.5" y="82">APR</text>
          <text x="125" y="82">MAY</text><text x="147.5" y="82">JUN</text><text x="170" y="82">JUL</text><text x="192.5" y="82">AUG</text>
          <text x="215" y="82">SEP</text><text x="237.5" y="82">OCT</text><text x="260" y="82">NOV</text><text x="282.5" y="82">DEC</text>
        </g>
        <g stroke="#eee" stroke-width=".4">
          <line x1="24" y1="85" x2="296" y2="85"/><line x1="24" y1="92" x2="296" y2="92"/><line x1="24" y1="99" x2="296" y2="99"/>
          <line x1="24" y1="106" x2="296" y2="106"/><line x1="24" y1="113" x2="296" y2="113"/><line x1="24" y1="120" x2="296" y2="120"/>
        </g>
        <rect x="24" y="86" width="70" height="6" rx="1" fill="var(--navy)"/><text x="59" y="90.2" text-anchor="middle" font-size="3.2" fill="#fff">Event - 01</text>
        <rect x="70" y="93" width="66" height="6" rx="1" fill="var(--red)"/><text x="103" y="97.2" text-anchor="middle" font-size="3.2" fill="#fff">Event - 02</text>
        <rect x="96" y="100" width="64" height="6" rx="1" fill="#888"/><text x="128" y="104.2" text-anchor="middle" font-size="3.2" fill="#fff">Event - 03</text>
        <rect x="138" y="107" width="90" height="6" rx="1" fill="var(--orange)"/><text x="183" y="111.2" text-anchor="middle" font-size="3.2" fill="#fff">Event - 04</text>
        <rect x="138" y="114" width="142" height="6" rx="1" fill="#6f9be0"/><text x="209" y="118.2" text-anchor="middle" font-size="3.2" fill="#fff">Event - 05</text>
        <rect x="222" y="121" width="74" height="6" rx="1" fill="var(--green)"/><text x="259" y="125.2" text-anchor="middle" font-size="3.2" fill="#fff">Event - 06</text>
        <rect y="162" width="320" height="18" fill="var(--navy)"/>
        <text x="11" y="174" font-size="8" fill="#fff">BrightTownsForum</text>
        <text x="294" y="173" text-anchor="end" font-size="3" fill="#fff">BrightTownsForum  |  Copyright 2017</text>
        <circle cx="302" cy="171.5" r="3.5" fill="var(--blue)"/><text x="302" y="172.7" text-anchor="middle" font-size="3" fill="#fff">47</text>
      </svg>
    </section>

  </main>
</div>
</body>
</html>
```